Need Help having my business card stand out

I am the owner of Birchway Canine Training and would like for my business cards to stand out. I have been trying to keep designing them myself but I can't get what I have in my head on the card. I will try my best to post templates that I like for inspirations. I want something unique but elegant. I don't want in to look cartoony or cheesy. It needs to pop in a pet shop but also in a coffee shop or gym.

Target Market(s)

Dog owners, Married ,No young kids Jr High school kids and up (maybe kids on the way) Executives, Stay at home moms/wives, Small business owners

Industry/Entity Type

Dog Training

Contact Information for Business Card

Lowell Spratt, 281-904-3376, info@birchwaycanine.example, www.birchwaycanine.example

Colors

Designer to choose colors to be used in the design.

Requirements
Must have
• my logo
Should not have
• Cursive lettering

```html
<!DOCTYPE html>
<html lang="en">
<head>
<meta charset="utf-8">
<title>Birchway Canine Training – Business Card</title>
<link rel="stylesheet" href="https://fonts.googleapis.com/css2?family=Jost:wght@300;400;600;700&family=Crimson+Text:wght@400&display=swap">
<style>
  :root {
    --backdrop: #4b4b4d;
    --card-white: #ffffff;
    --ink: #161616;
    --brand-blue: #0b31a6;
    --on-blue: #ffffff;
    --shadow: rgba(0, 0, 0, 0.35);
  }
  * { box-sizing: border-box; margin: 0; padding: 0; }
  html, body {
    width: 1200px;
    height: 1000px;
    overflow: hidden;
  }
  body {
    background: var(--backdrop);
    position: relative;
    font-family: "Jost", "Futura", sans-serif;
  }
  .card {
    position: absolute;
    top: 180px;
    width: 380px;
    height: 640px;
    border-radius: 30px;
    background: var(--card-white);
    overflow: hidden;
    box-shadow: 0 14px 30px var(--shadow);
  }
  /* Front: name side */
  .card--front { left: 170px; }
  .portrait-area {
    position: absolute;
    left: 0;
    top: 70px;
    width: 205px;
    height: 570px;
    background: linear-gradient(180deg, #2a2a2a 0%, #141414 45%, #101010 100%);
    border-radius: 0 120px 0 0;
  }
  .name-stack {
    position: absolute;
    top: 28px;
    left: 215px;
    display: flex;
    gap: 14px;
    writing-mode: vertical-rl;
  }
  .name-stack__name {
    font-weight: 600;
    font-size: 56px;
    letter-spacing: 4px;
    line-height: 1;
    color: var(--brand-blue);
    text-transform: uppercase;
  }
  .name-stack__title {
    font-weight: 300;
    font-size: 38px;
    letter-spacing: 8px;
    line-height: 1;
    color: var(--ink);
    text-transform: uppercase;
    padding-top: 70px;
  }

  /* Back: brand side */
  .card--back { left: 650px; }
  .brand-block {
    position: absolute;
    top: 110px;
    left: 0;
    width: 100%;
    text-align: center;
    padding: 0 40px;
  }
  .brand-block__tagline {
    font-weight: 400;
    font-size: 17px;
    letter-spacing: 3px;
    color: var(--ink);
    text-transform: uppercase;
    margin-bottom: 46px;
  }
  .brand-block__name {
    font-weight: 700;
    font-size: 50px;
    line-height: 1.08;
    color: var(--ink);
    text-transform: uppercase;
    letter-spacing: 1px;
  }
  .contact-band {
    position: absolute;
    left: 0;
    bottom: 0;
    width: 100%;
    height: 176px;
    background: var(--brand-blue);
    padding: 26px 28px;
    display: flex;
    flex-direction: column;
    gap: 8px;
    font-family: "Crimson Text", "Georgia", serif;
    color: var(--on-blue);
  }
  .contact-row {
    display: flex;
    align-items: center;
    gap: 14px;
    font-size: 23px;
    line-height: 1.3;
  }
  .contact-row__icon {
    width: 24px;
    height: 24px;
    flex: none;
  }
</style>
</head>
<body>

  <section class="card card--front" aria-label="Business card front">
    <div class="portrait-area" role="img" aria-label="Black and white illustration of a Doberman with cropped ears wearing a chain collar with a paw tag"></div>
    <div class="name-stack">
      <h1 class="name-stack__name">Lowell Spratt</h1>
      <p class="name-stack__title">Dog Trainer</p>
    </div>
  </section>

  <section class="card card--back" aria-label="Business card back">
    <div class="brand-block">
      <p class="brand-block__tagline">Your dog trainer for life</p>
      <p class="brand-block__name">Birchway<br>Canine<br>Training</p>
    </div>

    <div class="contact-band">
      <div class="contact-row">
        <svg class="contact-row__icon" viewBox="0 0 24 24" aria-hidden="true">
          <rect x="0" y="0" width="24" height="24" rx="3" fill="#ffffff"/>
          <path d="M8 5.5l2.2 3-1.4 1.4a9 9 0 0 0 5.3 5.3l1.4-1.4 3 2.2-1.5 2.5C11 18.5 5.5 13 5.5 7z" fill="var(--brand-blue)"/>
        </svg>
        <span>281-904-3376</span>
      </div>
      <div class="contact-row">
        <svg class="contact-row__icon" viewBox="0 0 24 24" aria-hidden="true">
          <rect x="0" y="0" width="24" height="24" rx="3" fill="#ffffff"/>
          <rect x="5" y="7" width="14" height="10" fill="none" stroke="var(--brand-blue)" stroke-width="1.6"/>
          <path d="M5 7l7 6 7-6" fill="none" stroke="var(--brand-blue)" stroke-width="1.6"/>
        </svg>
        <span>info@birchwaycanine.example</span>
      </div>
      <div class="contact-row">
        <svg class="contact-row__icon" viewBox="0 0 24 24" aria-hidden="true">
          <rect x="0" y="0" width="24" height="24" rx="3" fill="#ffffff"/>
          <circle cx="12" cy="12" r="6.5" fill="none" stroke="var(--brand-blue)" stroke-width="1.5"/>
          <ellipse cx="12" cy="12" rx="2.8" ry="6.5" fill="none" stroke="var(--brand-blue)" stroke-width="1.3"/>
          <path d="M5.5 12h13" stroke="var(--brand-blue)" stroke-width="1.3"/>
        </svg>
        <span>www.birchwaycanine.example</span>
      </div>
    </div>
  </section>

</body>
</html>
```